Business Card Design

We need a design for business cards for our company. We have a logo. We teach EMT's and we are based out of Virginia. The information that will need to add would be, name, title, phone number, email, address. On the back of the business card would be "We help you, help others"

Target Market(s)

People that want to become EMT's

Colors

Designer to choose colors to be used in the design.

Requirements
Must have
• company logo

```html
<!DOCTYPE html>
<html lang="en">
<head>
<meta charset="utf-8">
<title>Rescue Path Academy – Business Card</title>
<link rel="stylesheet" href="https://fonts.googleapis.com/css2?family=Montserrat:wght@500;600&family=Arimo:wght@400;700&display=swap">
<style>
  :root {
    --page-bg: #d9dadc;
    --card-dark: #1f2a35;
    --card-light: #ffffff;
    --brand-red: #c8172b;
    --ink-grey: #6b6f74;
    --ink-soft: #8d9297;
    --tagline-grey: #8f969d;
  }
  * { margin: 0; padding: 0; box-sizing: border-box; }
  html, body { width: 1200px; height: 880px; overflow: hidden; }
  body {
    background: var(--page-bg);
    font-family: "Arimo", Arial, sans-serif;
    display: flex;
    flex-direction: column;
    align-items: center;
    justify-content: space-evenly;
  }
  .card {
    width: 680px;
    height: 388px;
    border-radius: 22px;
    position: relative;
    overflow: hidden;
    box-shadow: 0 6px 18px rgba(0,0,0,0.18);
  }

  /* Back side */
  .card-back {
    background: var(--card-dark);
    display: flex;
    flex-direction: column;
    align-items: center;
    justify-content: center;
    gap: 70px;
  }
  .brand-name {
    font-family: "Montserrat", sans-serif;
    font-weight: 600;
    color: var(--brand-red);
    letter-spacing: 0.5px;
    display: flex;
    align-items: center;
    gap: 12px;
  }
  .brand-dot {
    width: 14px; height: 14px;
    background: var(--brand-red);
    border-radius: 50%;
    flex: none;
  }
  .card-back .brand-name { font-size: 38px; margin-top: 30px; }
  .tagline {
    font-family: "Montserrat", sans-serif;
    font-weight: 500;
    font-size: 15px;
    letter-spacing: 4px;
    color: var(--tagline-grey);
    text-transform: uppercase;
  }

  /* Front side */
  .card-front {
    background: var(--card-light);
    border-bottom: 8px solid var(--brand-red);
  }
  .card-front .brand-name {
    position: absolute;
    left: 44px;
    top: 70px;
    font-size: 36px;
  }
  .divider {
    position: absolute;
    left: 44px;
    right: 44px;
    top: 236px;
    height: 2px;
    background: var(--brand-red);
  }
  .holder {
    position: absolute;
    left: 44px;
    top: 178px;
  }
  .holder-name {
    font-size: 22px;
    font-weight: 700;
    text-transform: uppercase;
    color: var(--brand-red);
  }
  .holder-name .surname { color: var(--ink-grey); }
  .holder-title {
    font-size: 15px;
    color: var(--ink-soft);
    margin-top: 2px;
  }
  .address {
    position: absolute;
    right: 44px;
    top: 186px;
    text-align: right;
    font-size: 15px;
    line-height: 1.35;
    color: var(--ink-soft);
  }
  .contact-list {
    position: absolute;
    left: 44px;
    top: 256px;
    list-style: none;
    font-size: 16px;
    color: var(--ink-grey);
    line-height: 1.6;
  }
  .contact-list li { display: flex; align-items: center; gap: 12px; }
  .contact-list svg { width: 14px; height: 14px; flex: none; }
  .contact-list .accent { color: var(--brand-red); }
</style>
</head>
<body>

  <section class="card card-back" aria-label="Card back">
    <div class="brand-name"><span class="brand-dot"></span>RESCUE PATH ACADEMY</div>
    <p class="tagline">We help you, help others</p>
  </section>

  <section class="card card-front" aria-label="Card front">
    <div class="brand-name"><span class="brand-dot"></span>RESCUE PATH ACADEMY</div>

    <div class="holder">
      <p class="holder-name">Jordan <span class="surname">K. Reyes</span></p>
      <p class="holder-title">Managing Director</p>
    </div>

    <p class="address">PO BOX 480, Elm Avenue<br>2nd street, Richmond</p>

    <div class="divider"></div>

    <ul class="contact-list">
      <li>
        <svg viewBox="0 0 14 14" aria-hidden="true"><rect x="3" y="1" width="8" height="12" rx="1.5" fill="none" stroke="#c8172b" stroke-width="1.6"/></svg>
        +00 000 00000000
      </li>
      <li>
        <svg viewBox="0 0 14 14" aria-hidden="true"><rect x="1" y="3" width="12" height="9" fill="#c8172b"/><path d="M1 3 L7 8 L13 3" fill="none" stroke="#fff" stroke-width="1.3"/></svg>
        info@rescuepathmail.com
      </li>
      <li>
        <svg viewBox="0 0 14 14" aria-hidden="true"><circle cx="7" cy="7" r="6" fill="#c8172b"/><path d="M1 7 H13 M7 1 C4 4 4 10 7 13 M7 1 C10 4 10 10 7 13" fill="none" stroke="#fff" stroke-width="0.9"/></svg>
        <span>www.<span class="accent">rescuepathweb</span>.com</span>
      </li>
    </ul>
  </section>

</body>
</html>
```